TOP NOTCH CATALOG RE-DESIGN FOR A NATIONAL BRAND

This Project needs to be redesigned with a new look and feel we will use all the same tires and keep the same writing we will only change the model numbers from QZ to VR then the number
please visit www.valmortires.com for feel of site which will direct your imagination

Target Market(s)

Our Target Market is Truck Drivers throughout the USA

Industry/Entity Type

Trucking Company

Font styles to use
Serif

Requirements
Must have
• Yellow and Black this signify our Brand see attached Logo
Nice to have
• Lion since our logo is that shows a strong product
Should not have
• other tires other than what is listed

```html
<!DOCTYPE html>
<html lang="en">
<head>
<meta charset="utf-8">
<title>Valmor Tires – Catalog Cover</title>
<link href="https://fonts.googleapis.com/css2?family=Roboto+Slab:wght@300;400;700&display=swap" rel="stylesheet">
<style>
  :root {
    --page-bg: #e9e6e1;
    --navy: #1a1a3e;
    --navy-deep: #0f0f2a;
    --yellow: #d9a51c;
    --paper: #f1f1f1;
    --ink: #1b1b1b;
    --grey-text: #6b6b6b;
    --title-grey: #6f6f6f;
    --white: #ffffff;
  }
  * { margin: 0; padding: 0; box-sizing: border-box; }
  html, body {
    width: 1200px; height: 804px; overflow: hidden;
    background: var(--page-bg);
    font-family: "Roboto Slab", Georgia, serif;
  }
  .cover {
    position: absolute; left: 330px; top: 20px;
    width: 540px; height: 764px;
    background: var(--paper);
    overflow: hidden;
    box-shadow: 0 6px 22px rgba(0,0,0,.22);
  }
  .hero {
    position: absolute; left: 0; top: 0; width: 100%; height: 340px;
    background: radial-gradient(ellipse 60% 55% at 52% 38%, #7e7e8c 0%, #45455e 45%, var(--navy) 75%, var(--navy-deep) 100%);
  }
  .tire-photo {
    position: absolute; left: 55px; top: 95px;
    width: 430px; height: 150px;
    border-radius: 70px;
    background: linear-gradient(100deg, #2a2a30 0%, #55555c 30%, #b4b4bb 58%, #8a8a92 78%, #3a3a42 100%);
    box-shadow: 0 18px 26px rgba(0,0,0,.45);
  }
  .hero-lines { position: absolute; left: 0; top: 0; }
  .brand-diamond {
    position: absolute; left: 50%; top: 340px;
    width: 150px; height: 150px;
    transform: translate(-50%, -50%) rotate(45deg);
    background: var(--yellow);
    outline: 4px solid var(--white);
    box-shadow: 0 4px 14px rgba(0,0,0,.25);
  }
  .brand-name {
    position: absolute; left: 50%; top: 340px;
    transform: translate(-50%, -50%);
    font-weight: 700; font-size: 15px; letter-spacing: .5px;
    color: var(--ink); white-space: nowrap;
  }
  .title {
    position: absolute; left: 0; width: 100%; top: 462px;
    text-align: center; font-weight: 300; font-size: 50px; line-height: 1;
  }
  .title .first { color: var(--yellow); }
  .title .second { color: var(--title-grey); }
  .title-rule {
    position: absolute; left: 70px; width: 400px; top: 530px;
    height: 1px; background: var(--ink);
  }
  .mission {
    position: absolute; left: 75px; width: 390px; top: 542px;
    text-align: center; font-size: 10.5px; line-height: 1.5;
    color: var(--grey-text); font-weight: 300;
  }
  .footer-band {
    position: absolute; left: 0; bottom: 0; width: 100%; height: 128px;
    background: var(--yellow);
  }
  .site-link {
    position: absolute; left: 50%; top: 50%;
    transform: translate(-50%, -50%);
    border: 1px solid var(--white);
    padding: 9px 26px;
    color: var(--white); font-size: 14px; font-weight: 400; letter-spacing: .3px;
    white-space: nowrap;
  }
</style>
</head>
<body>
  <main class="cover">
    <section class="hero">
      <div class="tire-photo" role="img" aria-label="Photo of four alloy-wheel tires lined up on a dark studio floor"></div>
    </section>
    <svg class="hero-lines" width="540" height="340" viewBox="0 0 540 340" aria-hidden="true">
      <line x1="0" y1="60" x2="540" y2="300" stroke="#ffffff" stroke-opacity=".4" stroke-width="1"/>
      <line x1="430" y1="0" x2="70" y2="340" stroke="#ffffff" stroke-opacity=".4" stroke-width="1"/>
    </svg>

    <div class="brand-diamond" aria-hidden="true"></div>
    <div class="brand-name">VALMOR TIRES</div>

    <h1 class="title"><span class="first">Valmor</span> <span class="second">Tires</span></h1>
    <div class="title-rule"></div>
    <p class="mission">At Valmor Tires our mission is to earn and develop long lasting relationships with our customers and business partners, through responsive actions, a dedication to quality and the highest standard of manufacturing.</p>

    <footer class="footer-band">
      <span class="site-link">www.valmortires.com</span>
    </footer>
  </main>
</body>
</html>
```